Zielgruppe
Die Velorin Akademie bietet Kurse, Seminare & Coachings im Bereich der Kommunikation / Persönlichkeitsentwicklung an.
Folgendes Angebot besteht zur Zeit:
Seminare:
- 'Erste Schritte im Dialog', eine Einführung in die Kommunikation.
- 'Heitere Töchter, ruhige Väter' zum Thema Erziehung.
- 'Reifen mit Gelassenheit', zum Thema Älter werden und den Umgang damit.
Kurse:
- 'Gewaltfreie Kommunikation', Übungsgruppe
Coaching:
- Einzelsitzungen mit Hypnose
Ps: im Anhang unter 'Angabot_Vorlage.pdf' finden Sie mehr Infos zu den einezlenen Angebote.
Aufgabenstellung
Bitte berücksichtigen Sie, dass bereits ein Logo besteht (siehe Anhang).
Vom gesamteindruck her sollte die Website aufgeräumt, übersichtlich, harmonisch, freundlich & frisch wirken.
Es wäre super, wenn die Website authentisch wirkt (und weniger '0815 Business Website').
Bitte bedenken Sie, dass die Website sich an Private richtet, die sich nach einem 'strahlenderen & unbeschwerterem Lebene sehnen'.
Wir haben bereits viele Persönlichkeiten stärken können und möchten dies auch witerhin mit viel Herzblut machen.

```html
<!DOCTYPE html>
<html lang="de">
<head>
<meta charset="utf-8">
<title>Velorin Akademie – Startseite</title>
<link rel="stylesheet" href="https://fonts.googleapis.com/css2?family=Quicksand:wght@400;500;600&display=swap">
<style>
:root{
  --stage:#e6e7ef;
  --page:#ffffff;
  --ink:#2d2d2d;
  --ink-soft:#4a4a4a;
  --muted:#9a9a9a;
  --pill:rgba(40,40,40,.78);
  --field:#f3f3f3;
  --footer:#f1f1f1;
  --white:#ffffff;
  --caption:rgba(60,60,60,.72);
}
*{box-sizing:border-box;margin:0;padding:0}
html,body{width:1200px;height:2354px;overflow:hidden;background:var(--stage)}
body{font-family:"Quicksand",sans-serif;color:var(--ink)}
.stage{position:relative;width:1313px;height:2576px;transform:scale(.913938);transform-origin:0 0}
.abs{position:absolute}

/* shared photo tones */
.hero-photo{background:
   linear-gradient(to bottom,rgba(255,255,255,0) 55%,#fff 100%),
   radial-gradient(ellipse at 52% 38%,#eef2f3 0%,rgba(238,242,243,0) 40%),
   linear-gradient(to bottom,#f4f6f7 0%,#dfe7ea 22%,#a3bfc8 42%,#82a5b0 58%,#b9c6c7 76%,#ffffff 100%);
  opacity:.92}
.ph1{background:linear-gradient(160deg,#5d7a3c 0%,#93ad6e 40%,#c8cfc0 70%,#a9aba6 100%)}
.ph2{background:linear-gradient(170deg,#e6eae6 0%,#a8b8a0 35%,#6f8a66 65%,#5e7560 100%)}
.ph3{background:linear-gradient(175deg,#eef0f0 0%,#b7a17a 40%,#8b7a5e 65%,#5a6a6a 100%)}
.ph4{background:linear-gradient(180deg,#e6eaee 0%,#d3dde4 45%,#9fb1bb 75%,#8c8a80 100%)}
.ph5{background:linear-gradient(135deg,#eeeae0 0%,#ddd3b5 35%,#ebe6e0 60%,#f4f2f0 100%)}

/* ---------- desktop page ---------- */
.page{position:absolute;left:40px;top:48px;width:1008px;height:1778px;background:var(--page);overflow:hidden;box-shadow:0 6px 24px rgba(0,0,0,.08)}
.page .diamond{left:-37px;top:187px;width:736px;height:736px}
.page .hero-photo{left:0;top:0;width:1008px;height:590px}
.page .brand{left:56px;top:42px;width:190px;text-align:center;color:var(--ink);font-weight:500}
.page .brand .name{font-size:30px;line-height:36px}
.page .brand .sub{font-size:14px;letter-spacing:2.4px;margin-top:6px}
.page .nav{top:53px;font-size:17px;letter-spacing:.4px;line-height:30px;color:var(--ink)}
.page .nav.active{left:320px;border:2px solid var(--ink-soft);border-radius:5px;padding:0 10px}
.page .cta{left:85px;top:434px;width:501px;height:50px;background:var(--pill);border-radius:13px;color:var(--white);
  font-size:16.5px;font-weight:500;display:flex;align-items:center;padding-left:22px;gap:12px;white-space:nowrap}
.page .newsletter{left:600px;top:435px;width:327px;height:50px;border-radius:13px;overflow:hidden;display:flex}
.page .newsletter .label{width:138px;background:var(--pill);color:var(--white);font-size:16.5px;font-weight:500;display:flex;align-items:center;padding-left:16px}
.page .newsletter .field{flex:1;background:var(--field);font-size:16.5px;display:flex;align-items:center;padding-left:15px}
.page .intro-mark{left:100px;top:660px;width:350px;text-align:center;color:var(--muted);font-weight:500}
.page .intro-mark .name{font-size:56px;line-height:70px}
.page .intro-mark .sub{font-size:26px;letter-spacing:3.6px;margin-top:14px;white-space:nowrap}
.page .intro-text{left:504px;top:605px;width:448px;font-size:14.6px;line-height:17.4px;color:var(--ink)}
.page .intro-text p+p{margin-top:17px}
.page .btn-outline{left:509px;top:838px;height:31px;border:2px solid var(--ink-soft);border-radius:5px;padding:0 12px;font-size:16.5px;line-height:27px}
.tile{position:absolute;width:267px;height:267px;box-shadow:0 2px 6px rgba(0,0,0,.15)}
.tile .photo{position:absolute;inset:0}
.tile .caption{position:absolute;left:12px;bottom:10px;background:var(--caption);color:#f4f4f4;
  font-size:16px;line-height:19px;padding:8px 22px 8px 8px;border-radius:14px;text-transform:uppercase;white-space:nowrap}
.tile .go{position:absolute;right:18px;bottom:16px;width:20px;height:20px}
.page .footer{left:0;top:1599px;width:1008px;height:179px;background:var(--footer);color:var(--ink-soft);font-size:15.5px;line-height:20px}
.page .footer .f{position:absolute}

/* ---------- mobile column ---------- */
.mobile{position:absolute;left:1077px;top:48px;width:196px;height:1552px;background:var(--page);overflow:hidden;box-shadow:0 6px 18px rgba(0,0,0,.08)}
.mobile .hero-photo{left:0;top:0;width:196px;height:250px}
.mobile .diamond{left:-40px;top:80px;width:190px;height:190px}
.mobile .brand{left:10px;top:10px;font-size:8px;font-weight:500;line-height:10px;color:var(--ink)}
.mobile .brand small{display:block;font-size:4px;letter-spacing:.6px;line-height:6px}
.mobile .burger{left:170px;top:12px;width:17px;height:14px}
.mobile .cta{left:15px;top:153px;width:166px;height:17px;background:var(--pill);border-radius:5px;color:var(--white);
  font-size:5.3px;font-weight:500;display:flex;align-items:center;padding-left:7px;white-space:nowrap}
.mobile .newsletter{left:33px;top:180px;width:132px;height:14px;border-radius:4px;overflow:hidden;display:flex;font-size:5.3px}
.mobile .newsletter .label{width:52px;background:var(--pill);color:var(--white);display:flex;align-items:center;padding-left:6px}
.mobile .newsletter .field{flex:1;background:var(--field);display:flex;align-items:center;padding-left:5px}
.mobile .intro-mark{left:16px;top:208px;width:100px;text-align:center;color:var(--muted);font-weight:500}
.mobile .intro-mark .name{font-size:17px;line-height:22px}
.mobile .intro-mark .sub{font-size:6.5px;letter-spacing:1px;margin-top:2px;white-space:nowrap}
.mobile .intro-text{left:13px;top:256px;width:174px;font-size:5.2px;line-height:6.8px;color:var(--ink)}
.mobile .intro-text p+p{margin-top:6px}
.mobile .btn-outline{left:12px;top:347px;height:12px;border:1px solid var(--ink-soft);border-radius:3px;padding:0 7px;font-size:5px;line-height:10px}
.mobile .tile{width:161px;height:161px}
.mobile .tile .caption{left:8px;bottom:6px;font-size:6px;line-height:7.5px;padding:4px 14px 4px 4px;border-radius:6px;opacity:.8}
.mobile .footer{left:0;top:1318px;width:196px;height:234px;background:var(--footer);color:var(--ink-soft);font-size:9.5px;line-height:12.5px;text-align:center}
.mobile .footer p{position:absolute;left:0;width:196px}
</style>
</head>
<body>
<div class="stage">

  <main class="page">
    <svg class="abs diamond" viewBox="0 0 736 736" aria-hidden="true">
      <defs><linearGradient id="dg" x1="0" y1="0" x2="0" y2="1">
        <stop offset="0" stop-color="#d6d6d6" stop-opacity=".7"/><stop offset="1" stop-color="#f1f1f1"/></linearGradient></defs>
      <polygon points="368,0 736,368 368,736 0,368" fill="url(#dg)"/>
    </svg>
    <div class="abs hero-photo" role="img" aria-label="Foto: Ein Paar umarmt sich mit erhobenen Armen auf einem Steg vor nebligen Bergen und einem See"></div>

    <div class="abs brand"><div class="name">Velorin</div><div class="sub">VELORIN AKADEMIE</div></div>
    <nav>
      <span class="abs nav active">HOME</span>
      <span class="abs nav" style="left:485px">ANGEBOTE</span>
      <span class="abs nav" style="left:680px">KONTANKT</span>
      <span class="abs nav" style="left:871px">ÜBER UNS</span>
    </nav>

    <div class="abs cta">JETZT KOSTENFREIES ERSTGESPRÄCH VEREINBAREN
      <svg width="16" height="14" viewBox="0 0 16 14" aria-hidden="true"><path d="M2 2l5 5-5 5M8 2l5 5-5 5" fill="none" stroke="#fff" stroke-width="2"/></svg>
    </div>
    <div class="abs newsletter"><span class="label">NEWSLETTER:</span><span class="field">E-Mail</span></div>

    <div class="abs intro-mark"><div class="name">Velorin</div><div class="sub">VELORIN AKADEMIE</div></div>
    <div class="abs intro-text">
      <p>Lorem ipsum dolor sit amet, consetetur sadipscing elitr, sed diam nonumy eirmod tempor invidunt ut labore et dolore magna aliquyam erat, sed diam voluptua. At vero eos et accusam et justo duo dolores et ea rebum. Stet clita kasd gubergren no sea takimata sanctus est Lorem ipsum dolor sit amet. Lorem ipsum dolor sit amet, consetetur sadipscing elitr, sed diam nonumy eirmod tempor invidunt ut labore et dolore magna aliquyam erat, sed diam voluptua.</p>
      <p>At vero eos et accusam et justo duo dolores et ea rebum. Stet clita kasd gubergren, no se takimata sanctus est Lorem ipsum dolor sit amet. Lorem ipsum</p>
    </div>
    <span class="abs btn-outline">ÜBER UNS</span>

    <section>
      <div class="tile" style="left:74px;top:960px"><div class="photo ph1" role="img" aria-label="Foto: Eltern begleiten ihr Kind beim Radfahren im Park"></div><div class="caption">Heitere Töchter,<br>ruhige Väter</div><svg class="go" viewBox="0 0 20 20" aria-hidden="true"><path d="M3 3l7 7-7 7M10 3l7 7-7 7" fill="none" stroke="#1e1e1e" stroke-width="3"/></svg></div>
      <div class="tile" style="left:370px;top:960px"><div class="photo ph2" role="img" aria-label="Foto: Älteres Paar Arm in Arm vor grüner Hügellandschaft"></div><div class="caption">Reifen mit<br>Gelassenheit</div><svg class="go" viewBox="0 0 20 20" aria-hidden="true"><path d="M3 3l7 7-7 7M10 3l7 7-7 7" fill="none" stroke="#1e1e1e" stroke-width="3"/></svg></div>
      <div class="tile" style="left:667px;top:960px"><div class="photo ph3" role="img" aria-label="Foto: Lachende Freundinnen umarmen sich in den Bergen"></div><div class="caption">Erste Schritte<br>im Dialog</div><svg class="go" viewBox="0 0 20 20" aria-hidden="true"><path d="M3 3l7 7-7 7M10 3l7 7-7 7" fill="none" stroke="#1e1e1e" stroke-width="3"/></svg></div>
      <div class="tile" style="left:74px;top:1256px"><div class="photo ph4" role="img" aria-label="Foto: Person mit Rucksack springt vor einem See in die Luft"></div><div class="caption">Gibt es Auswege<br>aus der Realität?</div><svg class="go" viewBox="0 0 20 20" aria-hidden="true"><path d="M3 3l7 7-7 7M10 3l7 7-7 7" fill="none" stroke="#1e1e1e" stroke-width="3"/></svg></div>
      <div class="tile" style="left:370px;top:1256px"><div class="photo ph5" role="img" aria-label="Foto: Lächelnde Frau mit einem Luftballon"></div><div class="caption">Coaching mit<br>Hypnose</div><svg class="go" viewBox="0 0 20 20" aria-hidden="true"><path d="M3 3l7 7-7 7M10 3l7 7-7 7" fill="none" stroke="#1e1e1e" stroke-width="3"/></svg></div>
    </section>

    <footer class="abs footer">
      <span class="f" style="left:96px;top:40px">VELORIN AKADEMIE</span>
      <span class="f" style="left:96px;top:78px">Lindenweg 7</span>
      <span class="f" style="left:96px;top:113px">54321 Beispielstadt</span>
      <span class="f" style="left:307px;top:78px">Tel. 0456 7812093</span>
      <span class="f" style="left:307px;top:113px">Fax 0456 7812094</span>
      <span class="f" style="left:509px;top:78px">info@velorin-akademie.de</span>
      <span class="f" style="left:509px;top:113px">www.velorin-akademie.de</span>
      <span class="f" style="left:770px;top:78px">Impressum</span>
      <span class="f" style="left:770px;top:113px">Datenschutz</span>
    </footer>
  </main>

  <aside class="mobile">
    <svg class="abs diamond" viewBox="0 0 190 190" aria-hidden="true">
      <polygon points="95,0 190,95 95,190 0,95" fill="#e4e4e4" opacity=".7"/>
    </svg>
    <div class="abs hero-photo" role="img" aria-label="Foto: Ein Paar umarmt sich mit erhobenen Armen vor nebligen Bergen"></div>
    <div class="abs brand">Velorin<small>VELORIN AKADEMIE</small></div>
    <svg class="abs burger" viewBox="0 0 17 14" aria-hidden="true"><path d="M0 1.5h17M0 7h17M0 12.5h17" stroke="#333" stroke-width="2"/></svg>
    <div class="abs cta">JETZT KOSTENFREIES ERSTGESPRÄCH VEREINBAREN »</div>
    <div class="abs newsletter"><span class="label">NEWSLETTER:</span><span class="field">E-Mail</span></div>
    <div class="abs intro-mark"><div class="name">Velorin</div><div class="sub">VELORIN AKADEMIE</div></div>
    <div class="abs intro-text">
      <p>Lorem ipsum dolor sit amet, consetetur sadipscing elitr, sed diam nonumy eirmod tempor invidunt ut labore et dolore magna aliquyam erat, sed diam voluptua. At vero eos et accusam et justo duo dolores et ea rebum. Stet clita kasd gubergren no sea takimata sanctus est Lorem ipsum dolor sit amet. Lorem ipsum dolor sit amet, consetetur sadipscing elitr, sed diam nonumy eirmod tempor invidunt ut labore et dolore magna aliquyam erat, sed diam voluptua.</p>
      <p>At vero eos et accusam et justo duo dolores et ea rebum. Stet clita kasd gubergren, no se takimata sanctus est Lorem ipsum dolor sit amet. Lorem ipsum</p>
    </div>
    <span class="abs btn-outline">ÜBER UNS</span>

    <div class="tile" style="left:19px;top:393px"><div class="photo ph1" role="img" aria-label="Foto: Eltern begleiten ihr Kind beim Radfahren"></div><div class="caption">Heitere Töchter,<br>ruhige Väter</div></div>
    <div class="tile" style="left:19px;top:571px"><div class="photo ph2" role="img" aria-label="Foto: Älteres Paar Arm in Arm"></div><div class="caption">Reifen mit<br>Gelassenheit</div></div>
    <div class="tile" style="left:19px;top:752px"><div class="photo ph3" role="img" aria-label="Foto: Lachende Freundinnen in den Bergen"></div><div class="caption">Erste Schritte<br>im Dialog</div></div>
    <div class="tile" style="left:19px;top:933px"><div class="photo ph4" role="img" aria-label="Foto: Person springt vor einem See in die Luft"></div><div class="caption">Gibt es Auswege<br>aus der Realität?</div></div>
    <div class="tile" style="left:19px;top:1116px"><div class="photo ph5" role="img" aria-label="Foto: Lächelnde Frau mit Luftballon"></div><div class="caption">Coaching mit<br>Hypnose</div></div>

    <footer class="abs footer">
      <p style="top:34px">VELORIN AKADEMIE</p>
      <p style="top:62px">Lindenweg 7<br>54321 Beispielstadt</p>
      <p style="top:99px">Tel. 0456 7812093<br>Fax 0456 7812094</p>
      <p style="top:137px">info@velorin-akademie.de<br>www.velorin-akademie.de</p>
      <p style="top:175px">Impressum<br>Datenschutz</p>
    </footer>
  </aside>

</div>
</body>
</html>
```